Media Services Start-up -- Corporate Website and Logo Design. Inspiration required!

We need a logo design and corporate website design, including coding, for our start-up business.
Vennatra’s value proposition is based on bringing together media content from a vast number of geographies globally, adding human and AI curation, translation and editing, and delivering the content using tailored customer interfaces. On the one hand, the business brings together media coverage from all over the world, and on the other it brings together content, human skills and technology to deliver a supreme customer experience.
Vennatra is a B2B media monitoring and analytics business with emphasis on global customers. Vennatra's service offering is centred around sourcing media content from different markets, processing, storing and delivering the content and insights derived from it using an online platform / mobile app.
The messaging we want to create through the logo is:
- Global scope
- Speed of delivery
- Cost-efficiency
- Multi-lingual
- Tailor-made
- Trustworthy
Target Market(s)
Business to business, PR / Communications, Media, Marketing
Logo Text
Vennatra
Coding
Coded - Design and coding required
Number of Pages Required
5+ page
Font styles to use
Other font styles liked:
- See Design Brief for details
Colors
Designer to choose colors to be used in the design.

```html
<!DOCTYPE html>
<html lang="en">
<head>
<meta charset="utf-8">
<title>Our People – Vennatra Media Intelligence</title>
<link href="https://fonts.googleapis.com/css2?family=Roboto:wght@400;500;700&display=swap" rel="stylesheet">
<style>
:root{
  --teal:#3bb3a0;
  --ink:#0d0d0d;
  --header:#131313;
  --white:#ffffff;
  --muted:#e6e6e6;
}
*{margin:0;padding:0;box-sizing:border-box}
html,body{width:1200px;height:514px;overflow:hidden;background:var(--ink)}
body{font-family:'Roboto',Arial,sans-serif;color:var(--white);position:relative}
.hero-backdrop{position:absolute;left:0;top:0;width:1200px;height:479px;
  background:radial-gradient(circle at 600px 320px,#3a3a3a 0,#1f1f1f 160px,#111 420px,#0a0a0a 700px)}
.site-header{position:absolute;left:0;top:0;width:1200px;height:85px;background:rgba(19,19,19,.92)}
.brand{position:absolute;left:141px;top:14px;display:flex;align-items:center;gap:10px}
.brand-mark{width:36px;height:36px;border-radius:50%;background:var(--teal)}
.brand-name{font-size:13px;line-height:14.5px;font-weight:400;color:var(--white);text-transform:uppercase;letter-spacing:.2px}
.contact{position:absolute;top:11px;display:flex;align-items:center;gap:9px;font-size:14.5px;color:var(--white)}
.contact svg{width:27px;height:27px}
.contact.phone{left:733px}
.contact.mail{left:900px}
.main-nav{position:absolute;left:498px;top:54px;display:flex;gap:25px;font-size:14.5px}
.main-nav a{color:var(--white);text-decoration:none}
.main-nav a.active{color:var(--teal);font-weight:500}
.sign-in{position:absolute;left:975px;top:49px;width:85px;height:28px;background:var(--teal);color:var(--white);
  font-size:15px;display:flex;align-items:center;justify-content:center;text-decoration:none;letter-spacing:.3px}
.people{position:absolute;left:0;top:130px;width:1200px}
.people h1{text-align:center;font-size:32px;font-weight:700;line-height:1}
.lead{width:880px;margin:18px auto 0;text-align:center;font-size:13.6px;font-weight:700;line-height:22.5px}
.facts{list-style:none;position:absolute;left:141px;top:140px;width:880px}
.facts li{position:relative;padding-left:30px;font-size:14.2px;line-height:22.6px;margin-bottom:14.5px;color:var(--muted)}
.facts li svg{position:absolute;left:0;top:4px;width:15px;height:15px}
.site-footer{position:absolute;left:0;top:479px;width:1200px;height:35px;background:var(--teal)}
.copyright{position:absolute;left:141px;top:9px;font-size:13px;color:var(--white)}
.social{position:absolute;left:1000px;top:10px;display:flex;gap:12px}
.social span{width:15px;height:15px;border-radius:50%;background:var(--white)}
</style>
</head>
<body>
<div class="hero-backdrop" role="img" aria-label="Dark night city skyline with a person facing a glowing globe, surrounded by connected network lines and circular industry icons"></div>

<header class="site-header">
  <div class="brand">
    <span class="brand-mark"></span>
    <span class="brand-name">Vennatra<br>Media<br>Intelligence</span>
  </div>
  <div class="contact phone">
    <svg viewBox="0 0 27 27" aria-hidden="true"><circle cx="13.5" cy="13.5" r="12.5" fill="none" stroke="#fff" stroke-width="1.2"/><path d="M9.5 8.5l2.2-.6 1.2 2.8-1.3 1c.7 1.5 1.7 2.5 3.2 3.2l1-1.3 2.8 1.2-.6 2.2c-4.3.3-8.8-4.2-8.5-8.5z" fill="#fff"/></svg>
    <span>+1 555 014 2086</span>
  </div>
  <div class="contact mail">
    <svg viewBox="0 0 27 27" aria-hidden="true"><circle cx="13.5" cy="13.5" r="12.5" fill="none" stroke="#fff" stroke-width="1.2"/><rect x="8" y="9.5" width="11" height="8" fill="#fff"/><path d="M8 9.5l5.5 4.5 5.5-4.5" fill="none" stroke="#131313" stroke-width="1"/></svg>
    <span>hello@vennatra.net</span>
  </div>
  <nav class="main-nav">
    <a href="#">Home</a>
    <a href="#">Solutions</a>
    <a href="#">Our Approach</a>
    <a href="#" class="active">Our People</a>
    <a href="#">Our Technology</a>
  </nav>
  <a href="#" class="sign-in">SIGN IN</a>
</header>

<main class="people">
  <h1>Our People</h1>
  <p class="lead">We are a team of experienced and competent media intelligence professionals with 10+ years experience in delivering global solutions to the PR &amp; Communications community.</p>
  <ul class="facts">
    <li><svg viewBox="0 0 15 15" aria-hidden="true"><rect x="1" y="1" width="13" height="13" rx="2" fill="none" stroke="#3bb3a0" stroke-width="2"/><path d="M4.3 7.6l2.2 2.2 4.2-4.4" fill="none" stroke="#3bb3a0" stroke-width="1.8"/></svg>Vennatra is a team of content and media intelligence professionals, bringing media, communications, monitoring and measurement experience to its customers.</li>
    <li><svg viewBox="0 0 15 15" aria-hidden="true"><rect x="1" y="1" width="13" height="13" rx="2" fill="none" stroke="#3bb3a0" stroke-width="2"/><path d="M4.3 7.6l2.2 2.2 4.2-4.4" fill="none" stroke="#3bb3a0" stroke-width="1.8"/></svg>Vennatra’s team have in-market experience with media content in all EMEA markets, North America, South America and Asia.</li>
    <li><svg viewBox="0 0 15 15" aria-hidden="true"><rect x="1" y="1" width="13" height="13" rx="2" fill="none" stroke="#3bb3a0" stroke-width="2"/><path d="M4.3 7.6l2.2 2.2 4.2-4.4" fill="none" stroke="#3bb3a0" stroke-width="1.8"/></svg>The team consists of knowledge centres within the Finance, Automotive, FMCG, Government, Non Profit, Retail, Hospitality, Pharmaceuticals sectors around the world.</li>
  </ul>
</main>

<footer class="site-footer">
  <p class="copyright">Copyright © 2019 Vennatra Media Intelligence. All Rights Reserved.</p>
  <div class="social">
    <span role="img" aria-label="Social profile link"></span>
    <span role="img" aria-label="Social profile link"></span>
    <span role="img" aria-label="Social profile link"></span>
  </div>
</footer>
</body>
</html>
```